New Business Card Design Project LORVANTI-Italy

we are LORVANTI-Italy
our company in the market for 3 years we are luxury cosmetic company and its about time for a facelift :)
i will like to have elegant luxurious and unique business card
that will give the person that get it a unique, luxurious and elegant impression
I'm VERY OPEN FOR NEW IDEAS , even duo i add a few files of things that i see on line and i like them

i add my logo as well
my website is LORVANTI.COM
(if you would like to see the main style that we have)

Target Market(s)

adult that have money :)

Industry/Entity Type

Business

Contact Information for Business Card

Name - Dario Lorvanti
Position - CEO and CO Founder
address - 4817 E Halvern
telephone - 555-384-1926
email - dario@lorvanti.com
fax - 555-384-1926
website - LORVANTI.COM

Colors
000000
959595
fbee3e
ffffff

Requirements
Must have
• big logo in GOLD color
• elegant look
• impressive
Nice to have
• not must but maybe classy pattern background
• not must but maybe emblem
• maybe clear plastic business card
Should not have
• colors
• images

```html
<!DOCTYPE html>
<html lang="en">
<head>
<meta charset="utf-8">
<title>LORVANTI Italy – Business Card</title>
<link href="https://fonts.googleapis.com/css2?family=Cormorant+Garamond:wght@600&family=Open+Sans:wght@400&display=swap" rel="stylesheet">
<style>
  :root {
    --backdrop: #000000;
    --card: #1c1c1c;
    --gold: #dcb23c;
    --ink-light: #e4e4e4;
    --serif: "Cormorant Garamond", Georgia, serif;
    --sans: "Open Sans", Arial, sans-serif;
  }
  * { margin: 0; padding: 0; box-sizing: border-box; }
  html, body {
    width: 1200px; height: 900px; overflow: hidden;
    background: var(--backdrop);
  }
  .stage { position: relative; width: 1200px; height: 900px; }
  .card {
    position: absolute; top: 200px; width: 310px; height: 502px;
    background: var(--card);
  }
  .card--front { left: 265px; border-radius: 46px 0 46px 0; }
  .card--back  { left: 641px; border-radius: 0 46px 0 46px; }

  .brand-circle {
    position: absolute; border: 3px solid var(--gold); border-radius: 50%;
  }
  .card--front .brand-circle { left: 91px; top: 51px; width: 100px; height: 100px; }

  .brand-name {
    position: absolute; left: 0; width: 100%; text-align: center;
    font-family: var(--serif); font-weight: 600; color: var(--gold);
    letter-spacing: 1px;
  }
  .card--front .brand-name { top: 170px; font-size: 44px; left: -13px; }
  .brand-country {
    position: absolute; top: 232px; left: -13px; width: 100%; text-align: center;
    font-family: var(--serif); font-weight: 600; color: var(--gold);
    font-size: 18px; letter-spacing: 1px;
  }

  .holder { position: absolute; left: 27px; top: 303px; }
  .holder__name {
    font-family: var(--serif); font-weight: 600; color: var(--gold);
    font-size: 21px; letter-spacing: .5px; line-height: 24px;
  }
  .holder__role {
    font-family: var(--sans); color: var(--ink-light);
    font-size: 13px; line-height: 20px;
  }

  .contacts { position: absolute; left: 27px; top: 361px; list-style: none; }
  .contacts li, .address {
    display: flex; align-items: center; gap: 7px;
    font-family: var(--sans); color: var(--ink-light);
    font-size: 13px; line-height: 18px;
  }
  .contacts svg, .address svg { width: 11px; height: 11px; fill: var(--gold); flex: none; }
  .address { position: absolute; left: 25px; top: 450px; }
  .address svg { width: 12px; height: 15px; }

  .card--back .brand-circle { left: 53px; top: 148px; width: 204px; height: 204px; border-width: 4px; }
  .card--back .brand-name { top: 228px; font-size: 34px; }
  .back-web {
    position: absolute; top: 428px; width: 100%; text-align: center;
    font-family: var(--serif); font-weight: 600; color: var(--gold);
    font-size: 17px; letter-spacing: .5px;
  }
</style>
</head>
<body>
<main class="stage">
  <section class="card card--front">
    <div class="brand-circle"></div>
    <div class="brand-name">LORVANTI</div>
    <div class="brand-country">ITALY</div>

    <div class="holder">
      <div class="holder__name">DARIO LORVANTI</div>
      <div class="holder__role">CEO and CO Founder</div>
    </div>

    <ul class="contacts">
      <li>
        <svg viewBox="0 0 12 12" aria-hidden="true"><path d="M2.4 0.5l2 2.3-1 1.4c.7 1.5 2 2.8 3.5 3.5l1.4-1 2.3 2-1.2 2.2C4.6 10.6 1.4 7.4 0.3 2.2z"/></svg>
        555-384-1926
      </li>
      <li>
        <svg viewBox="0 0 12 12" aria-hidden="true"><path d="M3 0h6v3H3zM1 4h10v6H9v2H3v-2H1zM4 8v3h4V8z"/></svg>
        555-384-1926
      </li>
      <li>
        <svg viewBox="0 0 12 12" aria-hidden="true"><path d="M0 2h12v1L6 7 0 3zM0 4.5l6 4 6-4V10H0z"/></svg>
        dario@lorvanti.com
      </li>
      <li>
        <svg viewBox="0 0 12 12" aria-hidden="true"><path d="M6 0a6 6 0 1 0 0 12A6 6 0 0 0 6 0zm0 1.2c.8 0 1.5 2 1.6 4.2H4.4C4.5 3.2 5.2 1.2 6 1.2zM4.4 6.6h3.2C7.5 8.8 6.8 10.8 6 10.8S4.5 8.8 4.4 6.6z"/></svg>
        www.lorvanti.com
      </li>
    </ul>

    <div class="address">
      <svg viewBox="0 0 12 15" aria-hidden="true"><path d="M6 0a6 6 0 0 0-6 6c0 4 6 9 6 9s6-5 6-9a6 6 0 0 0-6-6zm0 3.5a2.5 2.5 0 1 1 0 5 2.5 2.5 0 0 1 0-5z"/></svg>
      4817 E Halvern
    </div>
  </section>

  <section class="card card--back">
    <div class="brand-circle"></div>
    <div class="brand-name">LORVANTI</div>
    <div class="back-web">WWW.LORVANTI.COM</div>
  </section>
</main>
</body>
</html>
```